Create the ONLY Supplement line for Male Entrepreneurs! (Verity Nine MD)

I need a label designed for a new supplement brand that I am launching.

There are five products so need a design that I can simply change the wording for each individual product

The brand name is called verity nine MD. The focus is male entrepreneurial health.

Target audience is men 35 to 55.

Concepts: the healthier you are in body the more money you will make in business.

Concept to copy: I want to make a clean minimalistic label mimicking Lansworth MD (google it and you'll see what I mean)

Target Market(s)

male entrepreneurs 35-55

Industry/Entity Type

Health Supplement

Colors

Designer to choose colors to be used in the design.

Requirements
Must have
• Modern classy design, similar to Lansworth MD.
Nice to have
• Highlight that the supplement is Doctor Approved.
Should not have
• No loud colors. Present it as high class.

```html
<!DOCTYPE html>
<html lang="en">
<head>
<meta charset="utf-8">
<title>Verity Nine MD – Omege 3 Label</title>
<link href="https://fonts.googleapis.com/css2?family=Montserrat:wght@300;400;500&display=swap" rel="stylesheet">
<style>
  :root {
    --page-bg: #ffffff;
    --label-bg: #ffffff;
    --label-border: #8c8c8c;
    --band: #e9ecef;
    --ink: #111111;
    --ink-soft: #2f2c28;
    --ink-muted: #7d8287;
    --heart: #e6e8eb;
  }
  * { margin: 0; padding: 0; box-sizing: border-box; }
  html, body {
    width: 1200px; height: 1200px; overflow: hidden;
    background: var(--page-bg);
  }
  .label {
    position: absolute;
    left: 250px; top: 70px;
    width: 700px; height: 1060px;
    background: var(--label-bg);
    border: 1.5px solid var(--label-border);
    overflow: hidden;
  }
  .band {
    position: absolute; left: 0; right: 0; top: 723px; bottom: 0;
    background: var(--band);
  }
  .brand {
    position: absolute; left: 0; right: 0; top: 270px;
    text-align: center;
    font-family: "Montserrat", sans-serif;
    font-weight: 400;
    color: var(--ink);
    font-size: 58px;
    line-height: 1;
    letter-spacing: 1px;
  }
  .heart {
    position: absolute; left: 296px; top: 500px; width: 108px; height: 100px;
  }
  .product-name {
    position: absolute; left: 45px; top: 650px;
    font-family: "Montserrat", sans-serif; font-weight: 400;
    font-size: 82px; line-height: 1; color: var(--ink-soft);
  }
  .product-type {
    position: absolute; left: 45px; top: 746px;
    font-family: "Montserrat", sans-serif; font-weight: 300;
    font-size: 46px; line-height: 1; color: var(--ink-muted);
  }
  .approval {
    position: absolute; left: 45px; top: 813px; width: 312px;
    border-top: 2px solid var(--ink-soft);
    border-bottom: 2px solid var(--ink-soft);
    height: 58px;
    font-family: "Montserrat", sans-serif; font-weight: 500;
    font-size: 28px; letter-spacing: 2px; color: var(--ink);
    line-height: 54px;
  }
  .count {
    position: absolute; left: 45px; top: 930px;
    display: flex; align-items: baseline; gap: 14px;
    font-family: "Montserrat", sans-serif; line-height: 1;
  }
  .count-number { font-size: 66px; font-weight: 400; color: var(--ink); }
  .count-unit { font-size: 46px; font-weight: 300; color: var(--ink-muted); }
</style>
</head>
<body>
  <div class="label">
    <div class="band"></div>
    <div class="brand">Verity Nine MD</div>
    <svg class="heart" viewBox="0 0 108 100" aria-hidden="true">
      <path d="M54 90 C30 70 10 54 10 32 C10 18 21 8 34 8 C43 8 50 13 54 20 C58 13 65 8 74 8 C87 8 98 18 98 32 C98 54 78 70 54 90 Z"
            fill="none" stroke="var(--heart)" stroke-width="9" stroke-linejoin="round"/>
    </svg>
    <div class="product-name">Omege 3</div>
    <div class="product-type">Dietary supplement</div>
    <div class="approval">Doctor Approved</div>
    <div class="count"><span class="count-number">90</span><span class="count-unit">Softgels</span></div>
  </div>
</body>
</html>
```